Boutique Technology Consultancy specialising is Electronic and physical security

We need to redo our existing outdated website. For your reference the link www.pelu.com.au

```html
<!DOCTYPE html>
<html lang="en">
<head>
<meta charset="utf-8">
<title>Pelu Services</title>
<link href="https://fonts.googleapis.com/css2?family=Montserrat:wght@500;600;700;800&family=Open+Sans:wght@400;600&display=swap" rel="stylesheet">
<style>
:root{
  --red:#c8221d;
  --ink:#1b1b1b;
  --black:#0c0c0c;
  --text:#4a4a4a;
  --muted:#666;
  --grey-bg:#f3f3f3;
  --white:#fff;
}
*{margin:0;padding:0;box-sizing:border-box}
html,body{width:1200px;height:4580px;overflow:hidden}
body{position:relative;background:var(--white);font-family:"Open Sans",sans-serif;color:var(--text)}
.abs{position:absolute}
.brand{font-family:"Montserrat",sans-serif;font-weight:800;letter-spacing:2px;display:flex;align-items:center;gap:12px}
.brand .dot{width:22px;height:22px;background:var(--red);border-radius:50%}
.btn{position:absolute;background:var(--red);color:#fff;font-size:14px;display:flex;align-items:center;justify-content:center;font-family:"Open Sans",sans-serif}

/* header */
.topbar{left:418px;top:0;width:782px;height:54px;background:var(--black);color:#fff;font-size:14px}
.topbar span{position:absolute;top:17px;display:flex;align-items:center;gap:8px}
.nav{top:74px;left:459px;display:flex;gap:29px;font-size:14.5px;color:var(--ink)}
.quote{left:944px;top:67px;width:145px;height:38px;font-size:14.5px}

/* hero */
.hero-photo{left:0;top:117px;width:1200px;height:730px;background:linear-gradient(100deg,#050608 0%,#0b1116 40%,#1d3a4a 62%,#3c5a6b 78%,#64788a 100%)}
.hero-welcome{left:354px;top:306px;color:#fff;font-size:27px;font-family:"Montserrat",sans-serif;font-weight:500}
.hero-brand{left:268px;top:360px;color:#fff;font-size:130px;line-height:1}
.hero-cta{left:356px;top:551px;width:145px;height:37px;font-size:14.5px}

/* section titles */
.title{width:1200px;text-align:center;left:0}
.title h2{font-family:"Montserrat",sans-serif;font-weight:700;font-size:38px;color:var(--ink);display:inline-flex;align-items:center;gap:14px}
.title h2 em{font-style:normal;color:var(--red)}
.title h2::before,.title h2::after{content:"";width:80px;height:3px;background:var(--red)}
.title p{font-size:21px;color:var(--muted);margin-top:6px;font-family:"Montserrat",sans-serif;font-weight:500}

/* cards */
.card{position:absolute;background:#fff;box-shadow:0 3px 14px rgba(0,0,0,.13);text-align:center}
.card .pic{height:206px;width:100%}
.card h3{font-family:"Montserrat",sans-serif;font-weight:700;font-size:21px;color:var(--ink);margin-top:48px}
.card p{font-size:14px;line-height:26px;color:var(--text);padding:8px 6px 0;white-space:nowrap}
.card.active{border-bottom:7px solid var(--red)}
.badge{position:absolute;left:50%;top:168px;margin-left:-42px;width:84px;height:84px;border-radius:50%;background:var(--red);border:4px solid #fff}
.pattern{position:absolute;background:#ececec;opacity:.6}
.arrow{position:absolute;width:20px;height:20px;border-radius:50%;display:flex;align-items:center;justify-content:center}
.arrow.off{background:#bdbdbd}
.arrow.on{background:#3a1412}

/* who we are */
.who-bg{left:0;top:1600px;width:1200px;height:646px;background:linear-gradient(110deg,#bfe6f4 0%,#e8f5fb 45%,#f7fbfd 60%,#d4eef9 85%,#aee0f4 100%)}
.who-text{left:620px;top:1776px;width:500px;text-align:center;font-size:14px;line-height:26px;color:var(--ink);white-space:nowrap}
.who-text p+p{margin-top:26px}

/* team */
.tcard{position:absolute;background:#fff;box-shadow:0 3px 14px rgba(0,0,0,.13);text-align:center}
.avatar{position:absolute;border-radius:50%;background:radial-gradient(circle at 50% 40%,#d8b9a6 0%,#c9a08c 35%,var(--red) 36%,var(--red) 100%)}
.tcard h3{font-family:"Montserrat",sans-serif;font-weight:700;font-size:21px;color:var(--ink)}
.tcard p{font-size:14.5px;color:var(--text);margin-top:2px}

/* contact */
.field{position:absolute;border-bottom:1.5px solid #999;font-size:13.5px;color:var(--ink);padding-bottom:8px}
.field.red{border-color:var(--red)}

/* footer */
.footer{left:0;top:4260px;width:1200px;height:320px;background:var(--black);color:#fff}
.footer h4{font-family:"Montserrat",sans-serif;font-weight:700;font-size:21px;position:absolute}
.footer ul{list-style:none;position:absolute;font-size:14px;line-height:26px}
.footer .ci{position:absolute;font-size:14px;display:flex;gap:8px;align-items:flex-start}
.news-input{left:789px;top:114px;width:296px;height:50px;background:#fff;color:#555;font-size:14px;padding:16px 8px}
</style>
</head>
<body>

<header>
  <div class="abs brand" style="left:110px;top:28px;font-size:58px;color:var(--ink)"><span class="dot"></span>PELU</div>
  <div class="abs topbar">
    <span style="left:42px"><svg width="15" height="12" viewBox="0 0 15 12"><rect x="1" y="1" width="13" height="10" fill="none" stroke="#fff" stroke-width="1.4"/><path d="M1 1l6.5 5.5L14 1" fill="none" stroke="#fff" stroke-width="1.4"/></svg>hello@pelu.com.au</span>
    <span style="left:308px"><svg width="12" height="14" viewBox="0 0 12 14"><path d="M2 1l3 0 1 3-2 1.5c1 2 2 3 4 4l1.5-2 3 1v3c-6 .5-11-4.5-10.5-10.5z" fill="#fff"/></svg>1300 555 018</span>
    <span style="left:524px"><svg width="12" height="14" viewBox="0 0 12 14"><circle cx="6" cy="4" r="3.2" fill="#fff"/><path d="M0 14c0-4 3-6 6-6s6 2 6 6z" fill="#fff"/></svg>Client Help Center</span>
  </div>
  <nav class="abs nav"><span>Welcome</span><span>Experience</span><span>Services</span><span>Team</span><span>About</span><span>Contact</span></nav>
  <div class="btn quote">Request a Quote</div>
</header>

<section>
  <div class="abs hero-photo" role="img" aria-label="Technician inspecting a server rack in a data centre"></div>
  <svg class="abs" style="left:0;top:680px" width="1200" height="170" viewBox="0 0 1200 170">
    <polygon points="0,81 1200,30 1200,170 0,170" fill="#fff"/>
    <polygon points="740,58 1200,20 1200,163" fill="var(--red)"/>
  </svg>
  <div class="abs hero-welcome">Welcome To</div>
  <div class="abs brand hero-brand">PELU</div>
  <div class="btn hero-cta">Get Started</div>
</section>

<section>
  <div class="abs title" style="top:822px"><h2>Our <em>Services</em></h2><p>Your Technology Projects Made Easy.</p></div>
  <div class="pattern" style="left:826px;top:926px;width:292px;height:190px"></div>
  <div class="arrow off" style="left:66px;top:1176px"><svg width="8" height="10"><path d="M6 1L2 5l4 4" stroke="#fff" stroke-width="2" fill="none"/></svg></div>
  <div class="arrow on" style="left:1112px;top:1176px"><svg width="8" height="10"><path d="M2 1l4 4-4 4" stroke="#fff" stroke-width="2" fill="none"/></svg></div>

  <div class="card" style="left:110px;top:958px;width:302px;height:413px">
    <div class="pic" role="img" aria-label="Consultant working at computer monitors" style="background:linear-gradient(135deg,#2a3440,#6f7d88 55%,#c9ced2)"></div>
    <span class="badge"></span>
    <h3>Strategy</h3>
    <p>Technology roadmaps,Master standards<br>Asset management plans</p>
  </div>
  <div class="card active" style="left:450px;top:958px;width:300px;height:497px">
    <div class="pic" role="img" aria-label="Laptop with glowing network circuitry" style="background:linear-gradient(135deg,#071a3a,#1a4f9a 55%,#0c2a5a)"></div>
    <span class="badge"></span>
    <h3>Technologies Including</h3>
    <p>Smart Buildings;Systems Integration;<br>Control Centres;CCTV;Access Control;<br>Smart Cards;Electronic Lockers;<br>Intruder Alarms;Staff Safety Alarms;<br>Retail Analytics;Intercoms;Internet of<br>Things;Networks; Wi-Fi</p>
  </div>
  <div class="card" style="left:788px;top:958px;width:301px;height:413px">
    <div class="pic" role="img" aria-label="Project team reviewing plans on a tablet" style="background:linear-gradient(135deg,#9aa3ab,#55606a 55%,#2d3339)"></div>
    <span class="badge"></span>
    <h3>Projects</h3>
    <p>Technical project management,<br>Witness testing,Procurement<br>Audit,Design,Procurement</p>
  </div>
</section>

<section>
  <div class="abs who-bg" role="img" aria-label="Glass office tower facade seen from below"></div>
  <svg class="abs" style="left:0;top:1525px" width="1200" height="132" viewBox="0 0 1200 132">
    <polygon points="0,0 0,132 800,75" fill="var(--red)"/>
    <polygon points="0,0 800,75 1200,78 1200,0" fill="#fff"/>
  </svg>
  <div class="pattern" style="left:132px;top:1700px;width:340px;height:200px;opacity:.4"></div>
  <div class="abs" role="img" aria-label="Analyst reviewing data on a monitor" style="left:156px;top:1730px;width:351px;height:247px;background:linear-gradient(135deg,#0c1a2e,#274a78 60%,#4d6f9a)"></div>
  <div class="abs" role="img" aria-label="Colleagues meeting around a laptop in an office" style="left:110px;top:1925px;width:233px;height:222px;background:linear-gradient(135deg,#2c2f36,#6d6a66 55%,#c1b8aa)"></div>
  <div class="abs" role="img" aria-label="Engineer standing in an illuminated server room" style="left:357px;top:1988px;width:244px;height:219px;background:linear-gradient(135deg,#02202e,#0f6f8a 50%,#3fd0e6)"></div>

  <div class="abs title" style="top:1662px;left:420px;width:900px"><h2>Who <em>We Are</em></h2><p>Your Technology Projects Made Easy.</p></div>
  <div class="abs who-text">
    <p>PELU Services was established in 2016 by Bevan Thorley to provide<br>technology consulting services to corporate and government<br>clients with a focus on:<br>Property/facilities management,Asset management, Development<br>and Construction</p>
    <p>In 2022, PELU Services merged Norvex Group into its operations,<br>bringing increased capacity and capability to the NSW office.</p>
    <p>PELU is a privately owned independent consultancy 100%<br>dedicatd to customer satisfaction. With experience in a range of<br>technologies such as internet of things, security systems, wi-fi,<br>building services networks, control centres and smart buildings,<br>our services include:</p>
  </div>
  <div class="btn" style="left:814px;top:2150px;width:109px;height:35px">Read More</div>
</section>

<section>
  <div class="abs title" style="top:2354px"><h2>Our <em>Team</em></h2><p>Your Technology Projects Made Easy.</p></div>
  <div class="pattern" style="left:1016px;top:2540px;width:104px;height:150px"></div>
  <div class="arrow off" style="left:66px;top:2684px"><svg width="8" height="10"><path d="M6 1L2 5l4 4" stroke="#fff" stroke-width="2" fill="none"/></svg></div>
  <div class="arrow on" style="left:1112px;top:2684px"><svg width="8" height="10"><path d="M2 1l4 4-4 4" stroke="#fff" stroke-width="2" fill="none"/></svg></div>

  <div class="tcard" style="left:110px;top:2576px;width:276px;height:217px"><div style="margin-top:132px"><h3>Warren Tilby</h3><p>PrincipalConsultant</p></div></div>
  <div class="avatar" role="img" aria-label="Portrait of principal consultant" style="left:168px;top:2519px;width:160px;height:160px"></div>

  <div class="tcard" style="left:459px;top:2576px;width:275px;height:296px;border-bottom:7px solid var(--red)"><div style="margin-top:150px"><h3>Dean Corliss</h3><p>Senior Consultant</p></div></div>
  <div class="avatar" role="img" aria-label="Portrait of senior consultant" style="left:504px;top:2480px;width:185px;height:185px"></div>
  <div class="btn" style="left:538px;top:2800px;width:118px;height:37px">View Details</div>

  <div class="tcard" style="left:807px;top:2576px;width:276px;height:217px"><div style="margin-top:132px"><h3>Evan Hartwell</h3><p>Senior Consultant</p></div></div>
  <div class="avatar" role="img" aria-label="Portrait of senior consultant" style="left:865px;top:2519px;width:160px;height:160px"></div>
</section>

<section>
  <div class="abs" style="left:0;top:2973px;width:1200px;height:766px;background:var(--grey-bg)"></div>
  <svg class="abs" style="left:0;top:2902px" width="1200" height="130" viewBox="0 0 1200 130">
    <polygon points="630,88 1200,0 1200,129" fill="var(--red)"/>
  </svg>
  <div class="abs title" style="top:3062px"><h2>Our <em>Experience</em></h2><p>Your Technology Projects Made Easy.</p></div>
  <div class="pattern" style="left:830px;top:3162px;width:292px;height:190px"></div>

  <div class="card" style="left:110px;top:3193px;width:302px;height:413px">
    <div class="pic" role="img" aria-label="Tall glass office tower against a blue sky" style="background:linear-gradient(180deg,#cfe3f5,#6b9cc9 60%,#2d5a88)"></div>
    <h3 style="margin-top:20px">Meridian Tower</h3>
    <p>Shared building network and security<br>systems integration consulting for this<br>iconic office tower which is managed by<br>Harcourt Property</p>
  </div>
  <div class="card" style="left:450px;top:3193px;width:300px;height:413px">
    <div class="pic" role="img" aria-label="Laptop with glowing network circuitry" style="background:linear-gradient(135deg,#071a3a,#1a4f9a 55%,#0c2a5a)"></div>
    <h3 style="margin-top:20px">Riverton Water</h3>
    <p>Critical Infrastructure Security Upgrade<br>for multiple water treatment sites<br>including perimeter fencing, CCTV,<br>access control and electric keying.</p>
  </div>
  <div class="card" style="left:788px;top:3193px;width:301px;height:413px">
    <div class="pic" role="img" aria-label="Project team reviewing plans on a tablet" style="background:linear-gradient(135deg,#9aa3ab,#55606a 55%,#2d3339)"></div>
    <h3 style="margin-top:20px">Southern Federal Bank</h3>
    <p>Security operations technology<br>automation and integration<br>consulting for SFB asset protection<br>services' security operations centre.</p>
  </div>
  <div class="btn" style="left:542px;top:3654px;width:118px;height:37px">View More</div>
</section>

<section>
  <div class="abs title" style="top:3835px"><h2>Contact <em>Us</em></h2><p>Your Technology Projects Made Easy.</p></div>
  <div class="field red" style="left:119px;top:3966px;width:446px">Name</div>
  <div class="field" style="left:652px;top:3966px;width:447px">Last Name</div>
  <div class="field" style="left:119px;top:4040px;width:446px">Phone</div>
  <div class="field" style="left:652px;top:4040px;width:447px">Email</div>
  <div class="field" style="left:119px;top:4114px;width:971px;padding-bottom:12px">Message</div>
  <div class="btn" style="left:542px;top:4178px;width:118px;height:37px">Submit</div>
</section>

<footer class="abs footer">
  <div class="abs brand" style="left:110px;top:64px;font-size:58px;color:#fff"><span class="dot"></span>PELU</div>
  <div class="abs" style="left:113px;top:174px;font-size:11px">© 2023 Pelu | All Rights Reserved</div>

  <h4 style="left:423px;top:62px">Quick Lins</h4>
  <ul style="left:426px;top:108px"><li>Welcome</li><li>Experience</li><li>Services</li><li>Team</li><li>About</li><li>Contact</li></ul>

  <h4 style="left:572px;top:62px">Contact Us</h4>
  <div class="ci" style="left:576px;top:112px"><svg width="14" height="11" viewBox="0 0 15 12"><rect x="1" y="1" width="13" height="10" fill="none" stroke="#fff" stroke-width="1.4"/><path d="M1 1l6.5 5.5L14 1" fill="none" stroke="#fff" stroke-width="1.4"/></svg>hello@pelu.com.au</div>
  <div class="ci" style="left:576px;top:169px"><svg width="11" height="15" viewBox="0 0 11 15"><rect x="1" y="1" width="9" height="13" rx="1.5" fill="none" stroke="#fff" stroke-width="1.4"/></svg>1300 555 018</div>
  <div class="ci" style="left:576px;top:221px;line-height:22px"><svg width="12" height="16" viewBox="0 0 12 16"><path d="M6 0a6 6 0 0 0-6 6c0 4.5 6 10 6 10s6-5.5 6-10a6 6 0 0 0-6-6z" fill="#fff"/><circle cx="6" cy="6" r="2.2" fill="#0c0c0c"/></svg><span>Level 2, 88 Harbour Rd,<br>Melbourne VIC 3000</span></div>

  <h4 style="left:789px;top:62px">Subscribe To Our Newsletter</h4>
  <div class="abs news-input">Enter Email Address</div>
  <svg class="abs" style="left:1040px;top:124px" width="34" height="30" viewBox="0 0 34 30"><path d="M2 14L32 2 24 28 16 18z" fill="#111"/><path d="M16 18L32 2" stroke="#fff" stroke-width="1.5"/></svg>
  <div class="btn" style="left:789px;top:176px;width:119px;height:39px">Submit</div>
</footer>

</body>
</html>
```